Meadowlark Property Review is a leading provider of residential appraisal and home inspection products in S

I need a business card/logo designed that obviously describes my business. We are a residential appraisal and home inspection company in Springfield, MO. We offer residential appraisals, home inspection, pest inspection and radon gas measurement. We have been in business for 18 years and hold state certified residential appraisal licenses and OBREX certified home inspection licenses. I have a logo that I really like and will attach, but would be open to new suggestions. I like more modern designs than traditional and would like a two sided card with our services, licenses and qualifications on the back.

```html
<!DOCTYPE html>
<html lang="en">
<head>
<meta charset="utf-8">
<title>Meadowlark Property Review – Business Card</title>
<link rel="stylesheet" href="https://fonts.googleapis.com/css2?family=Arimo:wght@400;700&family=Playfair+Display:wght@700&display=swap">
<style>
  :root {
    --bg: #d9d9d9;
    --card: #f4f4f2;
    --band-light: #ab8c62;
    --band-dark: #97754a;
    --accent: #ee9a1e;
    --brown-text: #a27b48;
    --brand: #8c6a40;
    --white: #ffffff;
  }
  html, body {
    margin: 0;
    width: 1200px;
    height: 864px;
    overflow: hidden;
    background: var(--bg);
    font-family: "Arimo", Arial, sans-serif;
  }
  .stage {
    width: 1200px;
    height: 864px;
    display: flex;
    align-items: center;
    justify-content: center;
    gap: 40px;
  }
  .card {
    position: relative;
    width: 540px;
    height: 310px;
    background: var(--card);
    box-shadow: 0 6px 18px rgba(0,0,0,0.18);
    overflow: hidden;
  }

  /* Front */
  .brand {
    position: absolute;
    top: 44px;
    left: 44px;
    display: flex;
    align-items: center;
    gap: 12px;
    color: var(--brand);
    font-weight: 700;
    font-size: 26px;
    letter-spacing: 0.2px;
  }
  .brand-mark {
    width: 18px;
    height: 18px;
    background: var(--accent);
  }
  .contact-band {
    position: absolute;
    left: 0;
    right: 0;
    top: 118px;
    bottom: 0;
    background: linear-gradient(160deg, var(--band-light), var(--band-dark));
    border-top: 5px solid var(--accent);
    color: var(--white);
  }
  .contact-list {
    position: absolute;
    right: 22px;
    top: 22px;
    margin: 0;
    padding: 0;
    list-style: none;
    text-align: right;
    font-size: 16px;
    line-height: 24px;
  }
  .contact-list li {
    display: flex;
    justify-content: flex-end;
    align-items: center;
    gap: 12px;
  }
  .contact-list svg {
    width: 16px;
    height: 16px;
    flex: none;
  }
  .address {
    position: absolute;
    left: 20px;
    right: 20px;
    bottom: 20px;
    margin: 0;
    font-size: 12px;
    white-space: nowrap;
  }

  /* Back */
  .services-title {
    position: absolute;
    top: 36px;
    left: 0;
    right: 0;
    margin: 0;
    text-align: center;
    padding-left: 150px;
    font-family: "Playfair Display", Georgia, serif;
    font-size: 34px;
    color: var(--brown-text);
  }
  .services {
    position: absolute;
    top: 96px;
    left: 40px;
    right: 30px;
    display: grid;
    grid-template-columns: 1fr 1px 1fr;
    column-gap: 14px;
    color: var(--brown-text);
    font-size: 17px;
  }
  .services ul {
    margin: 0;
    padding: 0;
    list-style: none;
    line-height: 30px;
  }
  .services-left { text-align: right; }
  .services li {
    display: flex;
    align-items: center;
    gap: 10px;
  }
  .services-left li { justify-content: flex-end; }
  .bullet {
    width: 7px;
    height: 7px;
    border-radius: 50%;
    background: var(--accent);
    box-shadow: 0 0 0 3px rgba(238,154,30,0.25);
    flex: none;
  }
  .divider {
    background: var(--brown-text);
    height: 190px;
  }
</style>
</head>
<body>
<main class="stage">
  <section class="card card-front" aria-label="Card front">
    <div class="brand"><span class="brand-mark"></span>Meadowlark Property Review</div>
    <div class="contact-band">
      <ul class="contact-list">
        <li>417-555-0142
          <svg viewBox="0 0 16 16" aria-hidden="true"><path fill="#fff" d="M2 6c0-2 2-3 6-3s6 1 6 3l-2 1-1-2H5L4 7 2 6zm2 2h8l1 6H3l1-6zm4 1.5a2 2 0 1 0 0 4 2 2 0 0 0 0-4z"/></svg>
        </li>
        <li>417-555-0187
          <svg viewBox="0 0 16 16" aria-hidden="true"><rect x="4" y="1" width="8" height="14" rx="1.5" fill="#fff"/><rect x="5.5" y="3" width="5" height="8" fill="#a27b48"/></svg>
        </li>
        <li>417-555-0163
          <svg viewBox="0 0 16 16" aria-hidden="true"><rect x="4" y="1" width="8" height="5" fill="#fff"/><rect x="1" y="6" width="14" height="7" rx="1" fill="#fff"/><rect x="4" y="9" width="8" height="6" fill="#fff" stroke="#a27b48"/></svg>
        </li>
        <li>info@meadowlarkreview.com
          <svg viewBox="0 0 16 16" aria-hidden="true"><rect x="1" y="3" width="14" height="10" fill="#fff"/><path d="M1 3l7 6 7-6" fill="none" stroke="#a27b48" stroke-width="1.2"/></svg>
        </li>
      </ul>
      <p class="address">Meadowlark Property Review, 482 W Linden Avenue; Suite C Springfield, MO 65807</p>
    </div>
  </section>

  <section class="card card-back" aria-label="Card back">
    <h2 class="services-title">Services</h2>
    <div class="services">
      <ul class="services-left">
        <li>Home inspection<span class="bullet"></span></li>
        <li>Property inspection<span class="bullet"></span></li>
        <li>Residential appraisal<span class="bullet"></span></li>
        <li>Termite inspection<span class="bullet"></span></li>
        <li>Radon gas measurement<span class="bullet"></span></li>
      </ul>
      <div class="divider"></div>
      <ul class="services-right">
        <li><span class="bullet"></span>Pre purchase inspection</li>
        <li><span class="bullet"></span>Thermal imaging</li>
        <li><span class="bullet"></span>Mechanical inspection</li>
        <li><span class="bullet"></span>Tax appeal</li>
        <li><span class="bullet"></span>Asset evaluation</li>
        <li><span class="bullet"></span>Energy audits</li>
      </ul>
    </div>
  </section>
</main>
</body>
</html>
```